International business needs business cards

Our company, DRV Ventures Inc. is in the business of supplying a range construction products with particular emphasis on CEMENT. We have developed our own brand - TORVAN SUPPLIES - with which to infiltrate the market. We are launching our brand of cement (TORVAN Type IS Cement) into the Caribbean which is unlike anything this market has ever seen. A monopoly has existed here for the past 60-odd years and the market has now opened to allow the importation of other brands and consumers are anxious and ready for change/improvement. We are very excited to be launching and want to make a great first impression. We will be conducting workshops and seminars (from government level to the hardware store owners) and we want our business card to give us the strong, confident introduction that we need.

Target Market(s)

construction; builders; engineers; home owners

Industry/Entity Type

Construction

Contact Information for Business Card

Marisol Depree
CEO
cell # 1 555 4180736
Ground floor,Lindell Plaza Suite 2734
George Town,Grand Cayman
Cayman Islands,KY1-4823
EMAIL: m.depree@drvventuresinc.example
web site drvventuresinc.example

COMPANY: skype info drv.ventures.example

second card
Yvette Brannock-Depree
CFO
CELL# 1 555 607 3941
George Town,Grand Cayman
Cayman Islands,KY1-4823
EMAIL: y.brannockdepree@drvventuresinc.example
website drvventuresinc.example

Requirements
Must have
• Business cards must display BOTH logos - DRV is the company and TORVAN is the brand.

```html
<!DOCTYPE html>
<html lang="en">
<head>
<meta charset="utf-8">
<title>DRV Ventures Inc. – Business Cards</title>
<link rel="stylesheet" href="https://fonts.googleapis.com/css2?family=Open+Sans:wght@400;600;700&display=swap">
<style>
  :root {
    --backdrop: #ece8e4;
    --card-light: #f4f4f4;
    --brand-red: #7f1518;
    --ink: #1d1d1d;
    --white: #ffffff;
    --silver: #c9c9c9;
  }
  html, body {
    margin: 0;
    width: 1200px;
    height: 900px;
    overflow: hidden;
    background: var(--backdrop);
    font-family: "Open Sans", Arial, sans-serif;
  }
  .canvas {
    position: relative;
    width: 1200px;
    height: 900px;
  }
  .card {
    position: absolute;
    width: 604px;
    height: 372px;
    border-radius: 18px;
    overflow: hidden;
    box-shadow: 0 10px 30px rgba(0,0,0,0.18);
  }
  /* Front */
  .card-front {
    left: 120px;
    top: 45px;
    background: var(--card-light);
  }
  .holder-name {
    position: absolute;
    top: 20px;
    left: 0;
    width: 100%;
    text-align: center;
    margin: 0;
    font-size: 21px;
    font-weight: 700;
    color: var(--brand-red);
  }
  .holder-title {
    position: absolute;
    top: 50px;
    left: 0;
    width: 100%;
    text-align: center;
    margin: 0;
    font-size: 14px;
    color: var(--ink);
  }
  .company-mark {
    position: absolute;
    top: 105px;
    left: 0;
    width: 100%;
    display: flex;
    justify-content: center;
    align-items: center;
    gap: 12px;
  }
  .company-mark .mark-square {
    width: 58px;
    height: 58px;
    background: var(--brand-red);
  }
  .company-mark .mark-name {
    font-size: 30px;
    font-weight: 700;
    color: var(--ink);
    line-height: 1;
  }
  .contact-list {
    position: absolute;
    top: 216px;
    left: 0;
    width: 100%;
    margin: 0;
    padding: 0;
    list-style: none;
    text-align: center;
    font-size: 15px;
    color: var(--ink);
  }
  .contact-list li {
    height: 25.5px;
    display: flex;
    justify-content: center;
    align-items: center;
    gap: 5px;
  }
  .contact-list svg {
    width: 11px;
    height: 11px;
    fill: var(--brand-red);
  }
  .address-band {
    position: absolute;
    left: 0;
    bottom: 0;
    width: 100%;
    height: 70px;
    background: var(--brand-red);
    color: var(--white);
    font-size: 15px;
    line-height: 25px;
    text-align: center;
    padding-top: 10px;
    box-sizing: border-box;
  }
  /* Back */
  .card-back {
    left: 527px;
    top: 491px;
    background: var(--brand-red);
  }
  .back-company {
    position: absolute;
    left: 40px;
    top: 120px;
    margin: 0;
    font-size: 64px;
    font-weight: 700;
    color: var(--white);
    line-height: 1;
  }
  .brand-mark {
    position: absolute;
    right: 50px;
    bottom: 52px;
    font-size: 18px;
    font-weight: 700;
    color: var(--silver);
    letter-spacing: 1px;
  }
</style>
</head>
<body>
<main class="canvas">
  <section class="card card-front" aria-label="Business card front">
    <h1 class="holder-name">Marisol Depree</h1>
    <p class="holder-title">CEO</p>
    <div class="company-mark">
      <span class="mark-square"></span>
      <span class="mark-name">DRV Ventures Inc.</span>
    </div>
    <ul class="contact-list">
      <li>
        <svg viewBox="0 0 24 24" aria-hidden="true"><path d="M6.6 10.8a15.1 15.1 0 0 0 6.6 6.6l2.2-2.2a1 1 0 0 1 1-.25 11.4 11.4 0 0 0 3.6.57 1 1 0 0 1 1 1V20a1 1 0 0 1-1 1A17 17 0 0 1 3 4a1 1 0 0 1 1-1h3.5a1 1 0 0 1 1 1c0 1.25.2 2.45.57 3.57a1 1 0 0 1-.25 1z"/></svg>
        1 555 4180736
      </li>
      <li>
        <svg viewBox="0 0 24 24" aria-hidden="true"><path d="M2 5h20v14H2z M2 5l10 8 10-8" /></svg>
        m.depree@drvventuresinc.example
      </li>
      <li>
        <svg viewBox="0 0 24 24" aria-hidden="true"><circle cx="12" cy="12" r="11"/></svg>
        www.drvventuresinc.example
      </li>
    </ul>
    <div class="address-band">
      Ground floor, Lindell Plaza Suite 2734 George Town, Grand Cayman<br>
      Cayman Islands, KY1-4823
    </div>
  </section>

  <section class="card card-back" aria-label="Business card back">
    <p class="back-company">DRV</p>
    <span class="brand-mark">TORVAN</span>
  </section>
</main>
</body>
</html>
```